Dorla's Cleaners new delivery postcard

We need to advertise for our new pick up and delivery dry cleaning/laundry service.
Mens Business Shirts $2.00
Pants $4.50
Skirts $5.00
Dry Clean Shirt/Blouse $5.00
Dress $9.00
2 Piece Suits $9.00
Updates
We would like to use a 5x7 size postcard, printed on both sides. We would like to add a discount to the card for 25% off of their first order, with the flyer.
We are a famly run dry cleaners. My name is Rosalind Tupper and my cell # is 614-302-7781. We are trying to expand our business to include free pick and delivery.
If possible can you use the logo I sent some where on the postcard? The phone # for the store is 614-295-3064.
Reason: Still need to get partners approval.

```html
<!DOCTYPE html>
<html lang="en">
<head>
<meta charset="utf-8">
<title>Dorla's Cleaners – Delivery Postcard</title>
<link rel="stylesheet" href="https://fonts.googleapis.com/css2?family=Luckiest+Guy&family=Montserrat:wght@300;400;500;600&display=swap">
<style>
  :root {
    --page-bg: #eceff2;
    --card-white: #ffffff;
    --sky-top: #f4fbff;
    --sky-mid: #a9d9f5;
    --sky-deep: #1f86d3;
    --panel-blue: #2d8fd6;
    --panel-edge: #1c6fb6;
    --brand-blue: #1a8ad6;
    --ink-navy: #153f8c;
    --accent-orange: #f47b20;
    --accent-green: #6fbf3a;
    --accent-yellow: #f6b81c;
    --strip-grey: #eef0f3;
    --fine-ink: #333a44;
  }
  * { box-sizing: border-box; margin: 0; padding: 0; }
  html, body {
    width: 1200px; height: 900px; overflow: hidden;
    background: var(--page-bg);
  }
  .postcard {
    position: absolute;
    width: 570px; height: 400px;
    background: var(--card-white);
    overflow: hidden;
    box-shadow: 0 6px 18px rgba(0,0,0,.18);
  }
  .postcard--front { left: 50px; top: 50px; }
  .postcard--back { left: 590px; top: 450px; }

  .display { font-family: "Luckiest Guy", "Arial Black", sans-serif; letter-spacing: .5px; }

  /* FRONT */
  .front-backdrop {
    position: absolute; inset: 0 0 70px 0;
    background:
      radial-gradient(circle at 75% 30%, rgba(255,255,255,.9), rgba(255,255,255,0) 45%),
      linear-gradient(180deg, var(--sky-top) 0%, var(--sky-mid) 55%, var(--sky-deep) 100%);
  }
  .brand {
    position: absolute; left: 28px; top: 22px;
    display: flex; align-items: center; gap: 10px;
  }
  .brand-mark { width: 44px; height: 44px; background: var(--ink-navy); }
  .brand-name { font-size: 30px; color: var(--brand-blue); line-height: 1; padding-top: 6px; }

  .price-panel {
    position: absolute; left: 14px; top: 108px;
    width: 272px; height: 184px;
    background: linear-gradient(180deg, var(--panel-blue), var(--panel-edge));
    border-radius: 8px;
    padding: 14px 20px 0 26px;
    box-shadow: 0 4px 10px rgba(0,0,0,.2);
  }
  .price-list { list-style: none; font-family: "Montserrat", sans-serif; font-weight: 400; color: #fff; font-size: 14.5px; }
  .price-list li { display: flex; justify-content: space-between; line-height: 26px; }

  .offer-bubble {
    position: absolute; left: 322px; top: 78px;
    width: 230px; height: 230px; border-radius: 50%;
    background: radial-gradient(circle at 40% 35%, #ffffff 0%, #e3f3fd 55%, #9fd2f3 100%);
    box-shadow: inset 0 0 18px rgba(31,134,211,.35);
    text-align: center; font-family: "Montserrat", sans-serif;
    padding-top: 56px;
  }
  .offer-rate { font-size: 58px; font-weight: 600; color: var(--accent-orange); line-height: 1; }
  .offer-word { font-size: 34px; font-weight: 500; color: var(--brand-blue); line-height: 1.05; }
  .offer-terms { font-size: 19px; font-weight: 500; color: var(--accent-green); }

  .call-now { position: absolute; left: 50px; top: 296px; font-size: 26px; color: #fff; }
  .front-strip { position: absolute; left: 0; right: 0; bottom: 0; height: 70px; background: var(--card-white); }
  .phone { color: var(--ink-navy); }
  .front-phone { position: absolute; left: 72px; top: 334px; font-size: 40px; }
  .fine-print {
    position: absolute; left: 404px; top: 328px;
    font-family: "Montserrat", sans-serif; font-size: 9.5px; font-weight: 500;
    color: var(--fine-ink); line-height: 1.2;
  }

  /* BACK */
  .back-art { position: absolute; inset: 0; }
  .back-brand { position: absolute; left: 22px; top: 24px; display: flex; align-items: center; gap: 10px; }
  .services {
    position: absolute; left: 110px; top: 66px; width: 320px;
    font-size: 15px; color: var(--accent-yellow); text-align: center; line-height: 1.25;
  }
  .headline { position: absolute; left: 70px; top: 148px; font-size: 28px; }
  .headline .free { color: var(--accent-green); }
  .headline .rest { color: var(--brand-blue); }
  .back-call { position: absolute; left: 44px; top: 236px; font-size: 26px; color: #fff; }
  .back-phone { position: absolute; left: 58px; top: 272px; font-size: 40px; }
</style>
</head>
<body>

<section class="postcard postcard--front" aria-label="Postcard front">
  <div class="front-backdrop" role="img" aria-label="Soft blue water and soap bubble background"></div>
  <div class="brand">
    <span class="brand-mark"></span>
    <span class="brand-name display">Dorla's Cleaners</span>
  </div>

  <div class="price-panel">
    <ul class="price-list">
      <li><span>Mens Business Shirts</span><span>$2.00</span></li>
      <li><span>Pants</span><span>$4.50</span></li>
      <li><span>Skirts</span><span>$5.00</span></li>
      <li><span>Dry Clean Shirt/Blouse</span><span>$5.00</span></li>
      <li><span>Dress</span><span>$9.00</span></li>
      <li><span>2 Piece Suits</span><span>$9.00</span></li>
    </ul>
  </div>

  <div class="offer-bubble">
    <div class="offer-rate">25%</div>
    <div class="offer-word">discount</div>
    <div class="offer-terms">on first order</div>
  </div>

  <div class="front-strip"></div>
  <div class="call-now display">Call NOW</div>
  <div class="front-phone phone display">614-295-3064</div>
  <p class="fine-print">*Card must be presented<br>No specialty items<br>One time use</p>
</section>

<section class="postcard postcard--back" aria-label="Postcard back">
  <svg class="back-art" width="570" height="400" viewBox="0 0 570 400" role="img" aria-label="Blue water and soap bubble background with white curved panel">
    <defs>
      <linearGradient id="back-sky" x1="0" y1="0" x2="0" y2="1">
        <stop offset="0" stop-color="#cfeafb"/>
        <stop offset="0.6" stop-color="#5fb3e8"/>
        <stop offset="1" stop-color="#1f86d3"/>
      </linearGradient>
      <linearGradient id="back-side" x1="0" y1="0" x2="0" y2="1">
        <stop offset="0" stop-color="#2a8bd4"/>
        <stop offset="1" stop-color="#1a6fbf"/>
      </linearGradient>
    </defs>
    <rect width="570" height="345" fill="url(#back-sky)"/>
    <rect x="440" y="0" width="130" height="345" fill="url(#back-side)"/>
    <path d="M0 0 H440 C470 80 470 220 380 280 C300 320 150 325 0 320 Z" fill="#ffffff" opacity="0.82"/>
    <path d="M440 0 C470 80 470 220 380 280 C300 320 150 325 0 320 L0 330 C160 334 310 330 392 288 C486 230 488 80 452 0 Z" fill="#6fbf3a"/>
    <rect y="345" width="570" height="55" fill="#eef0f3"/>
  </svg>
  <div class="back-brand">
    <span class="brand-mark"></span>
    <span class="brand-name display">Dorla's Cleaners</span>
  </div>
  <p class="services display">• Dry cleaning • Shirt laundry • Alterations<br>• Wedding dresses • Storage</p>
  <p class="headline display"><span class="free">Free</span> <span class="rest">Delivery &amp; Pick up</span></p>
  <div class="back-call display">Call NOW</div>
  <div class="back-phone phone display">614-295-3064</div>
</section>

</body>
</html>
```